4D Cradle Glimpse Luxury Ultrasound Billboard

Design a HIGH-END, MODERN billboard for my private prenatal ultrasound studio, 4D Cradle Glimpse, located in Pace, Florida.
This billboard will be viewed by drivers traveling at highway speeds, so it must be extremely clean, simple, and readable within 6 seconds.
About My Business
4D Cradle Glimpse is a private prenatal ultrasound studio specializing in:
Highest technology 4D/HD Ultrasounds
Early Gender Determination
Pregnancy Confirmation
I have been serving families for nearly 10 years and is known for creating a memorable experience, not just an ultrasound appointment.
Design Style
I DO NOT want:
Flowers
Leaves
Swirls
Glitter
Hearts everywhere
Busy backgrounds
Generic maternity stock graphics
I DO want:
Modern
Luxury
Upscale
Clean
Professional
Eye-catching
Premium medical spa feel
Colors
Use colors from my logo:
LOGO Green ( or a deep green)
Black
White
Soft Gold accents
Images:
Incorporate my professional headshot in a clean, modern way, logo, and the ultrasound images
Text
Keep wording minimal.
Primary Headline ( OPEN TO IDEAS) :
EXAMPLES ( WOULD RATHER SOMETHING MORE CATCHY)
" ADVANCED IMAGING. UNFORGETTABLE MOMENTS"
"MEET YOUR BABY BEFORE BIRTH"
Under headline:
4D Ultrasound • Early Gender • Pregnancy Confirmation
Business Name:
4D Cradle Glimpse
Private Prenatal Ultrasound Studio
Phone Number:
850-471-5923
Important
This billboard must be readable in 5–6 seconds from a moving vehicle.
Less text is better.
The phone number and business name must be visible from a distance.
The design should feel like a premium brand that immediately tells expecting parents:
“This is where I go to see my baby.”
Files Provided
Official logo
Headshot
Ultrasound images
Don’t make this look like a medical office billboard.
Make it look like a luxury baby experience billboard. That’s what separates 4D Cradle Glimpse from hospitals, OB offices, and all the new studios popping up around you. The emotional connection is what gets moms to book. ❤️
Billboard Size - 10.6” x 36”

```html
<!DOCTYPE html>
<html lang="en">
<head>
<meta charset="utf-8">
<title>4D Cradle Glimpse Billboard</title>
<link rel="stylesheet" href="https://fonts.googleapis.com/css2?family=Libre+Baskerville:wght@400;700&family=Montserrat:wght@500&display=swap">
<style>
  :root {
    --slate-green: #5f6e68;
    --slate-green-dark: #4f5d57;
    --soft-gold: #c39a3a;
    --white: #ffffff;
    --stage: #cfcfcf;
    --ink-grey: #5b6661;
    --photo-hair: #d9c39a;
    --photo-scrubs: #3f5a38;
    --scan-warm: #8a4a3e;
  }
  * { box-sizing: border-box; margin: 0; padding: 0; }
  html, body { width: 1200px; height: 1160px; overflow: hidden; }
  body { background: var(--stage); position: relative; }

  .billboard {
    position: absolute; left: 40px; top: 415px;
    width: 1120px; height: 330px;
    background: linear-gradient(90deg, #ffffff 0%, #f6f7f7 100%);
    overflow: hidden;
  }

  .headline-panel {
    position: absolute; left: 614px; top: 0; width: 506px; height: 240px;
    background: var(--slate-green);
    border-top-left-radius: 80px 60px;
  }

  .phone-band {
    position: absolute; left: 0; top: 240px; width: 464px; height: 90px;
    background: var(--slate-green);
    display: flex; align-items: center; gap: 12px; padding-left: 30px;
  }
  .phone-band svg { width: 38px; height: 38px; flex: none; }
  .phone-number {
    font-family: "Libre Baskerville", Georgia, serif; font-weight: 700;
    font-size: 44px; color: var(--white); letter-spacing: 0.5px;
  }

  .brand {
    position: absolute; left: 40px; top: 18px; width: 480px; text-align: center;
    font-family: "Libre Baskerville", Georgia, serif; font-weight: 700;
    color: var(--soft-gold); line-height: 1;
  }
  .brand-line-top { display: block; font-size: 66px; }
  .brand-line-name { display: block; font-size: 44px; margin-top: 14px; }

  .brand-rule {
    position: absolute; left: 74px; top: 186px; width: 416px; height: 2px;
    background: var(--soft-gold);
  }
  .brand-tagline {
    position: absolute; left: 40px; top: 208px; width: 480px; text-align: center;
    font-family: "Montserrat", Arial, sans-serif; font-weight: 500;
    font-size: 17px; letter-spacing: 1.2px; color: var(--ink-grey);
  }

  .headshot {
    position: absolute; left: 467px; top: 13px; width: 262px; height: 317px;
    border-radius: 120px 120px 0 0;
    background: linear-gradient(180deg, var(--photo-hair) 0%, #e9d3b5 45%, var(--photo-scrubs) 75%, #355030 100%);
  }

  .scan-photo {
    position: absolute; left: 653px; top: 224px; width: 102px; height: 102px;
    border-radius: 50%; border: 3px solid #6f7c77;
    background: radial-gradient(circle at 50% 50%, #b36c5c 0%, var(--scan-warm) 60%, #3a1f1a 100%);
  }

  .headline {
    position: absolute; left: 736px; top: 20px; width: 370px; text-align: center;
    font-family: "Libre Baskerville", Georgia, serif; line-height: 1;
  }
  .headline-intro { display: block; font-weight: 400; font-size: 37px; color: var(--white); }
  .headline-accent { display: block; font-weight: 700; font-size: 68px; color: var(--soft-gold); margin-top: 10px; }
  .headline-main { display: block; font-weight: 700; font-size: 80px; color: var(--white); margin-top: 0; }

  .services {
    position: absolute; left: 770px; top: 262px; list-style: none;
    font-family: "Libre Baskerville", Georgia, serif; font-size: 18.5px;
    color: var(--ink-grey); line-height: 25px;
  }
  .services li::before { content: "• "; }
  .services .service-pair span + span::before { content: " • "; }
</style>
</head>
<body>
  <section class="billboard" aria-label="4D Cradle Glimpse billboard">
    <div class="headline-panel"></div>

    <div class="brand">
      <span class="brand-line-top">4D</span>
      <span class="brand-line-name">Cradle Glimpse</span>
    </div>
    <div class="brand-rule"></div>
    <p class="brand-tagline">PRENATAL ULTRASOUND STUDIO</p>

    <div class="phone-band">
      <svg viewBox="0 0 24 24" aria-hidden="true">
        <path fill="#ffffff" d="M6.6 10.8a15.1 15.1 0 0 0 6.6 6.6l2.2-2.2a1 1 0 0 1 1-.25 11.4 11.4 0 0 0 3.6.57 1 1 0 0 1 1 1V20a1 1 0 0 1-1 1A17 17 0 0 1 3 4a1 1 0 0 1 1-1h3.5a1 1 0 0 1 1 1c0 1.25.2 2.45.57 3.57a1 1 0 0 1-.25 1z"/>
        <path fill="none" stroke="#ffffff" stroke-width="1.6" stroke-linecap="round" d="M14.5 6.5a4 4 0 0 1 3 3M14.5 2.8a7.8 7.8 0 0 1 6.7 6.7"/>
      </svg>
      <span class="phone-number">850-471-5923</span>
    </div>

    <div class="headshot" role="img" aria-label="Studio owner headshot in green scrubs, chin resting on hand"></div>
    <div class="scan-photo" role="img" aria-label="4D ultrasound image of twin babies"></div>

    <h1 class="headline">
      <span class="headline-intro">Meet Your Baby</span>
      <span class="headline-accent">BEFORE</span>
      <span class="headline-main">BIRTH</span>
    </h1>

    <ul class="services">
      <li class="service-pair"><span>4D Ultrasound</span><span>Early Gender</span></li>
      <li>Pregnancy Confirmation</li>
    </ul>
  </section>
</body>
</html>
```